Layout for site fence advertising - length approx. 250 cm x 125 cm

The advertising will later be printed on a PVC film and used for events or on sports fields.

Main services :
Your regional contact at
Real estate and business financing
independent insurance advice

```html
<!DOCTYPE html>
<html lang="en">
<head>
<meta charset="utf-8">
<title>RW Finanzberatung – Site Fence Banner</title>
<link href="https://fonts.googleapis.com/css2?family=Montserrat:wght@400;500;600;800&display=swap" rel="stylesheet">
<style>
  :root {
    --page-bg: #eef1f5;
    --banner-bg: #f1f7fc;
    --brand-blue: #2a5caf;
    --brand-grey: #5f5f5f;
    --wave-light: #dcedf9;
    --sky-bottom: #5f9bd6;
    --white: #ffffff;
    --photo-top: #d9c4b4;
    --photo-bottom: #2e2d38;
  }
  * { margin: 0; padding: 0; box-sizing: border-box; }
  html, body {
    width: 1035px; height: 1200px; overflow: hidden;
    background: var(--page-bg);
    font-family: "Montserrat", Arial, sans-serif;
  }
  .fence-banner {
    position: absolute; left: 0; top: 341px;
    width: 1035px; height: 518px;
    background: var(--banner-bg);
    overflow: hidden;
  }
  .wave-area {
    position: absolute; inset: 0;
    background: linear-gradient(160deg, var(--banner-bg) 0%, var(--wave-light) 55%, var(--banner-bg) 80%);
  }
  .bottom-fade {
    position: absolute; left: 0; right: 0; bottom: 0; height: 64px;
    background: linear-gradient(to bottom, rgba(241,247,252,0), var(--sky-bottom));
  }
  .portrait-area {
    position: absolute; left: 712px; top: 22px;
    width: 323px; height: 430px;
    background: linear-gradient(to bottom, var(--photo-top) 0%, var(--photo-top) 40%, var(--photo-bottom) 62%, var(--photo-bottom) 100%);
  }
  .contact-pill {
    position: absolute; left: 47px; top: 121px;
    width: 290px; height: 41px; border-radius: 21px;
    background: var(--brand-blue); color: var(--white);
    font-weight: 600; font-size: 18.5px; line-height: 41px;
    text-align: center;
  }
  .brand-lockup {
    position: absolute; left: 52px; top: 179px;
    display: flex; align-items: center; height: 140px;
  }
  .brand-circle {
    width: 132px; height: 132px; border-radius: 50%;
    border: 3px solid var(--brand-blue);
  }
  .brand-divider {
    width: 3px; height: 140px; background: var(--brand-grey);
    margin: 0 11px 0 18px;
  }
  .brand-text { padding-top: 8px; }
  .brand-name {
    color: var(--brand-blue); font-weight: 600; font-size: 25px;
    line-height: 30px; white-space: nowrap;
  }
  .brand-tagline {
    color: var(--brand-grey); font-weight: 500; font-size: 18px;
    line-height: 26px; white-space: nowrap; margin-top: 2px;
  }
  .service-headline {
    position: absolute; left: 51px; top: 345px;
    font-weight: 800; font-size: 35.5px; line-height: 37px;
    color: var(--brand-grey); white-space: nowrap;
  }
  .service-headline .accent { color: var(--brand-blue); }
  .service-sub {
    position: absolute; left: 51px; top: 419px;
    font-weight: 400; font-size: 21px; color: var(--brand-grey);
    letter-spacing: 0.4px; white-space: nowrap;
  }
</style>
</head>
<body>
  <section class="fence-banner">
    <div class="wave-area" role="img" aria-label="Decorative blue wave artwork across the banner background"></div>
    <div class="bottom-fade"></div>
    <div class="portrait-area" role="img" aria-label="Portrait photo of the regional advisor in a dark suit and white shirt"></div>

    <div class="contact-pill">Your Regional Contact at</div>

    <div class="brand-lockup">
      <div class="brand-circle"></div>
      <div class="brand-divider"></div>
      <div class="brand-text">
        <div class="brand-name">RW Finanzberatung GmbH</div>
        <div class="brand-tagline">Finanzieren, Versichern, Vorsorgen</div>
      </div>
    </div>

    <h1 class="service-headline">REAL ESTATE <span class="accent">AND BUSINESS<br>FINANCING</span></h1>
    <p class="service-sub">independent insurance advice</p>
  </section>
</body>
</html>
```